Business Card Design

Hi I need a business card designed, we already have the business name logo artwork and would like some concept ideas for the Bus Card layout.
On the back of the card i want to include the products and services that we offer.
We are a Plastics Sheeting manufacture based in Perth Australia.

                                       

We need a BC design for a company called Tarvo Plastics based in Perth Australia.

We supply from DIY to Trade & Industrial  Engineering Markets.

We specialise in:

·         Cut to size panels  (all shapes and sizes)

·         Plastics fabrication & Welding

·         Custom Designs

·         Plastic Repairs

·         PVC Pipe Slotting & PVC Pipe Threading

·         Supplier of all types of engineering plastics and profiles.

Including:           Acrylic / Clarvene

                               Polycarbonate / Dorvil

                               Prismatic Light Diffuser

                               Vantrib

                               HDPE / UHMWPE

                               PVC / PVC Foam

                               Nylon

                               HIPS

```html
<!DOCTYPE html>
<html lang="en">
<head>
<meta charset="utf-8">
<title>Tarvo Plastics – Business Card</title>
<link rel="stylesheet" href="https://fonts.googleapis.com/css2?family=Source+Sans+3:wght@400;600;700;800&display=swap">
<style>
  :root {
    --navy: #13245e;
    --blue: #1f86c9;
    --orange: #e8731c;
    --ink: #3a3a3a;
    --grey-line: #c9c9c9;
    --card: #ffffff;
    --backdrop: #e9e6e1;
  }
  * { box-sizing: border-box; margin: 0; padding: 0; }
  html, body {
    width: 1200px; height: 720px; overflow: hidden;
    background: var(--backdrop);
    font-family: "Source Sans 3", Arial, sans-serif;
    color: var(--ink);
  }
  .sheet {
    position: relative; width: 1200px; height: 720px;
    display: flex; align-items: center; justify-content: center; gap: 40px;
  }
  .card {
    position: relative; width: 560px; height: 320px;
    background: var(--card);
    box-shadow: 0 6px 18px rgba(0,0,0,.18);
    overflow: hidden;
  }

  /* Front */
  .front .corner-band { position: absolute; top: 0; right: 0; }
  .front .person {
    position: absolute; top: 10px; right: 18px; text-align: right; color: #fff;
  }
  .front .person-name { font-size: 17px; font-weight: 700; line-height: 1.1; }
  .front .person-title { font-size: 12px; font-weight: 400; }
  .brand {
    display: flex; align-items: center; gap: 10px;
    color: var(--navy); font-weight: 800; letter-spacing: -.5px;
  }
  .brand-mark { width: 18px; height: 18px; background: var(--navy); }
  .front .brand { position: absolute; left: 34px; top: 118px; font-size: 46px; }
  .contact-list {
    position: absolute; left: 34px; top: 208px;
    list-style: none; font-size: 13px; line-height: 19px;
  }
  .contact-list li { display: flex; align-items: center; gap: 7px; }
  .contact-list svg { width: 12px; height: 12px; fill: var(--navy); flex: none; }
  .front .legal { position: absolute; left: 34px; bottom: 16px; font-size: 12px; }
  .front .divider {
    position: absolute; left: 262px; top: 196px; width: 1px; height: 88px;
    background: var(--grey-line);
  }
  .address {
    position: absolute; left: 276px; top: 196px;
    font-size: 13px; line-height: 17px; font-style: normal;
  }

  /* Back */
  .back .brand { justify-content: center; margin-top: 22px; font-size: 40px; }
  .back .intro {
    text-align: center; color: var(--navy); font-weight: 700;
    font-size: 14px; line-height: 17px; margin-top: 8px;
  }
  .offer { display: flex; margin: 14px 26px 0; }
  .offer-col { padding-right: 14px; }
  .offer-col + .offer-col {
    padding-left: 22px; border-left: 1px solid var(--grey-line);
  }
  .offer-heading { color: var(--navy); font-weight: 700; font-size: 16px; margin-bottom: 3px; }
  .offer-list { list-style: none; font-size: 13px; line-height: 17px; }
  .offer-list li { position: relative; padding-left: 12px; }
  .offer-list li::before {
    content: ""; position: absolute; left: 0; top: 6px;
    width: 6px; height: 6px; border-radius: 50%; background: var(--orange);
  }
  .specialties { width: 300px; }
</style>
</head>
<body>
<main class="sheet">

  <section class="card front" aria-label="Card front">
    <svg class="corner-band" width="280" height="90" viewBox="0 0 280 90" role="img" aria-label="Corner accent band in navy and blue tones">
      <polygon points="40,0 280,0 280,90" fill="var(--navy)"/>
    </svg>
    <div class="person">
      <div class="person-name">Your Name</div>
      <div class="person-title">Title</div>
    </div>

    <div class="brand"><span class="brand-mark"></span>Tarvo Plastics</div>

    <ul class="contact-list">
      <li><svg viewBox="0 0 12 12"><path d="M3 1l2 2-1 1.5c.6 1.4 1.7 2.5 3 3L8.5 6.5l2 2L9.5 11C5 11 1 7 1 2.5z"/></svg>08 9400 3187</li>
      <li><svg viewBox="0 0 12 12"><rect x="3" y="0.5" width="6" height="11" rx="1"/></svg>123-456-7890</li>
      <li><svg viewBox="0 0 12 12"><rect x="1" y="4" width="10" height="6" rx="1"/><rect x="3" y="1" width="6" height="3"/></svg>08 9400 3188</li>
      <li><svg viewBox="0 0 12 12"><path d="M1 3h10v6H1z M1 3l5 3.5L11 3" /></svg>sales@tarvoplastics.com.au</li>
    </ul>
    <p class="legal">Tarvo Holdings Pty Ltd T/A Tarvo Plastics ABN: TBA</p>

    <div class="divider"></div>
    <address class="address">
      Unit 4/18 Harlow Circuit<br>
      Bramwell Vale WA 6162<br>
      PO Box 2240<br>
      Bramwell Vale DC WA 6981
    </address>
  </section>

  <section class="card back" aria-label="Card back">
    <div class="brand"><span class="brand-mark"></span>Tarvo Plastics</div>
    <p class="intro">The Products And Services That We Offer<br>Are Supplied From Diy To Trade &amp; Industrial Engineering Markets</p>

    <div class="offer">
      <div class="offer-col specialties">
        <h2 class="offer-heading">We specialise in:</h2>
        <ul class="offer-list">
          <li>Cut to size panels (all shapes and sizes)</li>
          <li>Plastics fabrication &amp; Welding</li>
          <li>Custom Designs</li>
          <li>Plastic Repairs</li>
          <li>PVC Pipe Slotting &amp; PVC Pipe Threading</li>
          <li>Supplier of all types of engineering plastics and profiles</li>
        </ul>
      </div>
      <div class="offer-col materials">
        <h2 class="offer-heading">Including:</h2>
        <ul class="offer-list">
          <li>Acrylic / Clarvene</li>
          <li>Polycarbonate / Dorvil</li>
          <li>Prismatic Light Diffuser</li>
          <li>Vantrib</li>
          <li>HDPE / UHMWPE</li>
          <li>PVC / PVC Foam</li>
          <li>Nylon</li>
          <li>HIPS</li>
        </ul>
      </div>
    </div>
  </section>

</main>
</body>
</html>
```